Oil and Gas Exploration and Production company needs a business card design

We need a business card design using our logo and colors in the logo. We want a mainstream design.

```html
<!DOCTYPE html>
<html lang="en">
<head>
<meta charset="utf-8">
<title>Vela Oil &amp; Gas — Business Card</title>
<link rel="stylesheet" href="https://fonts.googleapis.com/css2?family=Arvo:wght@700&family=Roboto:wght@400&display=swap">
<style>
  :root {
    --backdrop: #e8e5e0;
    --card-light: #f7f7f5;
    --card-dark: #1c1c1d;
    --ink: #111111;
    --gold: #c0922a;
    --text-grey: #4a4a4a;
    --white: #f5f5f3;
  }
  * { margin: 0; padding: 0; box-sizing: border-box; }
  html, body { width: 1200px; height: 960px; overflow: hidden; }
  body { background: var(--backdrop); position: relative; font-family: "Roboto", Arial, sans-serif; }

  .card { position: absolute; width: 601px; height: 343px; box-shadow: 0 3px 8px rgba(0,0,0,0.25); }
  .card--front { left: 314px; top: 113px; background: var(--card-light); }
  .card--back { left: 311px; top: 472px; background: var(--card-dark); }

  .accent-bar { position: absolute; left: 0; top: 67px; width: 15px; height: 38px; background: var(--ink); }
  .holder-name { position: absolute; left: 38px; top: 65px; font-family: "Arvo", Georgia, serif; font-weight: 700; font-size: 20px; letter-spacing: 0.5px; color: var(--ink); }
  .holder-title { position: absolute; left: 38px; top: 92px; font-family: "Arvo", Georgia, serif; font-weight: 700; font-size: 13px; letter-spacing: 0.5px; color: var(--gold); }
  .name-rule { position: absolute; left: 38px; top: 119px; width: 300px; height: 2px; background: linear-gradient(to right, var(--ink), rgba(17,17,17,0.15)); }

  .wordmark { position: absolute; font-family: "Arvo", Georgia, serif; font-weight: 700; text-align: left; }
  .wordmark__dot { position: absolute; border-radius: 50%; background: var(--gold); }
  .wordmark__name { position: absolute; line-height: 1; white-space: nowrap; }
  .wordmark__sub { position: absolute; line-height: 1; letter-spacing: 3px; white-space: nowrap; }

  .card--front .wordmark { left: 322px; top: 40px; width: 250px; height: 110px; color: var(--ink); }
  .card--front .wordmark__dot { left: 2px; top: 30px; width: 44px; height: 44px; }
  .card--front .wordmark__name { left: 52px; top: 8px; font-size: 66px; }
  .card--front .wordmark__sub { left: 52px; top: 82px; font-size: 23px; }

  .card--back .wordmark { left: 158px; top: 107px; width: 300px; height: 130px; color: var(--white); }
  .card--back .wordmark__dot { left: 0; top: 34px; width: 50px; height: 50px; }
  .card--back .wordmark__name { left: 48px; top: 2px; font-size: 84px; }
  .card--back .wordmark__sub { left: 60px; top: 100px; font-size: 27px; }

  .contact-list { position: absolute; left: 39px; top: 234px; list-style: none; }
  .contact-list li { display: flex; align-items: center; height: 19px; font-size: 14px; color: var(--text-grey); }
  .contact-list svg { width: 13px; height: 13px; margin-right: 9px; fill: var(--ink); }

  .address { position: absolute; right: 37px; top: 255px; text-align: right; font-size: 14px; line-height: 18px; color: var(--text-grey); font-style: normal; }

  .back-web { position: absolute; left: 0; width: 100%; top: 287px; text-align: center; font-size: 14px; letter-spacing: 4.2px; color: var(--white); }
</style>
</head>
<body>
  <section class="card card--front">
    <div class="accent-bar"></div>
    <h1 class="holder-name">DANIEL REYES</h1>
    <p class="holder-title">CEO/FOUNDER</p>
    <div class="name-rule"></div>

    <div class="wordmark">
      <span class="wordmark__dot"></span>
      <span class="wordmark__name">Vela</span>
      <span class="wordmark__sub">OIL &amp; GAS</span>
    </div>

    <ul class="contact-list">
      <li><svg viewBox="0 0 16 16"><path d="M3.5 1l2.5 3-1.5 2a9 9 0 0 0 5 5l2-1.5 3 2.5-1.5 2.5C7 15 1 9 1 2.5z"/></svg>555 201 4417</li>
      <li><svg viewBox="0 0 16 16"><path d="M4 0h8v16H4zM5.5 2v10h5V2zM7 13.2h2v1.3H7z" fill-rule="evenodd"/></svg>555 382 7105</li>
      <li><svg viewBox="0 0 16 16"><path d="M4 1h8v4H4zM1 6h14v7h-2v2H3v-2H1zM4.5 10v3.5h7V10z" fill-rule="evenodd"/></svg>555 619 2830</li>
      <li><svg viewBox="0 0 16 16"><path d="M1 3h14v1.5L8 9 1 4.5zM1 6.3l7 4.4 7-4.4V13H1z"/></svg>info@velaoilgas.com</li>
    </ul>

    <address class="address">
      2140 Birchwood Drive<br>
      Fairbanks, Alaska 99701<br>
      www.velaoilgas.com
    </address>
  </section>

  <section class="card card--back">
    <div class="wordmark">
      <span class="wordmark__dot"></span>
      <span class="wordmark__name">Vela</span>
      <span class="wordmark__sub">OIL &amp; GAS</span>
    </div>
    <p class="back-web">www.velaoilgas.com</p>
  </section>
</body>
</html>
```